Four in One (Flexible infographic for Content Management Industry)

See attachment.
A graphic depicting 4 products, where each can stand on its own and each can be combined with others, but where, if all are taken together, the best result is achieved (the "super product").
Intended use is web. See attached file as an example.
The most basic idea is as the attached diagram shows, where 4 rectangles are arranged in a quadrangle, with a middle rectangle in the center representing the combined 4 products. This concept is fine except it is a bit too obvious as it stands. We are looking for either a variation of this or another concept.
The audience is technical + professional + enterprise - NOT consumers. Hence the design should be conservative in nature.
We are aware of tools like as Canva or Pictogram where such graphics are available, but we are looking for something with a bit more imagination and flexibility.
This graphic should be targeted to web sites and be delivered with vector-based (SVG) graphics.

```html
<!DOCTYPE html>
<html lang="en">
<head>
<meta charset="utf-8">
<title>Four in One – Super Product</title>
<link rel="stylesheet" href="https://fonts.googleapis.com/css2?family=Montserrat:wght@600;700;800&display=swap">
<style>
  :root {
    --frame: #e6e7e9;
    --paper: #ffffff;
    --ink: #2f2f33;
    --hub-fill: #e6e7e9;
    --hub-ring: #2d2d30;
    --docs: #52a8b1;
    --security: #3b7480;
    --erp: #51658c;
    --digital: #3c4f60;
  }
  html, body {
    margin: 0;
    padding: 0;
    width: 1155px;
    height: 1200px;
    overflow: hidden;
    background: var(--paper);
  }
  .infographic {
    display: block;
    width: 1155px;
    height: 1200px;
    font-family: "Montserrat", Arial, sans-serif;
  }
  .canvas-frame { fill: var(--paper); stroke: var(--frame); stroke-width: 36; }
  .panel { fill: var(--paper); stroke-width: 24; stroke-linejoin: miter; }
  .panel--docs { stroke: var(--docs); }
  .panel--security { stroke: var(--security); }
  .panel--erp { stroke: var(--erp); }
  .panel--digital { stroke: var(--digital); }
  .rule { stroke-width: 3.5; }
  .rule--docs { stroke: var(--docs); }
  .rule--security { stroke: var(--security); }
  .rule--erp { stroke: var(--erp); }
  .rule--digital { stroke: var(--digital); }
  .panel-title { fill: var(--ink); font-weight: 700; }
  .panel-title--large { font-size: 40px; }
  .panel-title--small { font-size: 33px; }
  .panel-text { fill: var(--ink); font-weight: 600; font-size: 20px; }
  .feature { fill: var(--ink); font-weight: 600; font-size: 20.5px; }
  .tick { fill: none; stroke: var(--ink); stroke-width: 3; stroke-linecap: round; stroke-linejoin: round; }
  .hub-ring { fill: var(--hub-fill); stroke: var(--hub-ring); stroke-width: 20; }
  .hub-title { fill: var(--hub-ring); font-weight: 800; font-size: 86px; }
  .icon-halo { fill: var(--paper); }
  .icon-disc--docs { fill: var(--docs); }
  .icon-disc--security { fill: var(--security); }
  .icon-disc--erp { fill: var(--erp); }
  .icon-disc--digital { fill: var(--digital); }
  .glyph { fill: none; stroke: #ffffff; stroke-width: 3.5; stroke-linecap: round; stroke-linejoin: round; }
  .glyph-solid { fill: #ffffff; }
</style>
</head>
<body>
<svg class="infographic" viewBox="0 0 1606 1668" xmlns="http://www.w3.org/2000/svg" role="img" aria-label="Super Product: four combined solutions">
  <defs>
    <path id="tick" class="tick" d="M0 0 L5 5 L14 -5"/>
  </defs>

  <rect class="canvas-frame" x="0" y="0" width="1606" height="1668"/>

  <!-- Quadrant panels -->
  <path class="panel panel--docs" d="M766 794 L147 794 L147 337 A170 170 0 0 1 317 167 L766 167 Z"/>
  <path class="panel panel--security" d="M841 794 L1460 794 L1460 337 A170 170 0 0 0 1290 167 L841 167 Z"/>
  <path class="panel panel--erp" d="M766 872 L147 872 L147 1330 A170 170 0 0 0 317 1500 L766 1500 Z"/>
  <path class="panel panel--digital" d="M841 872 L1460 872 L1460 1330 A170 170 0 0 1 1290 1500 L841 1500 Z"/>

  <!-- Document Management -->
  <g class="quadrant quadrant--docs">
    <text class="panel-title panel-title--large" x="215" y="306" textLength="503" lengthAdjust="spacingAndGlyphs">Document Management</text>
    <line class="rule rule--docs" x1="220" y1="329" x2="725" y2="329"/>
    <text class="panel-text" text-anchor="end">
      <tspan x="741" y="377">Streamline document organization, access, and</tspan>
      <tspan x="741" y="402">collaboration with easier file storage and sharing,</tspan>
      <tspan x="741" y="427">leading to more efficient workflows .</tspan>
    </text>
    <use href="#tick" x="217" y="485"/><text class="feature" x="241" y="490">Centralized Document Control</text>
    <use href="#tick" x="217" y="510"/><text class="feature" x="241" y="515">Collaborative Workspace Integration</text>
    <use href="#tick" x="217" y="536"/><text class="feature" x="241" y="541">Automated Compliance Tracking</text>
    <use href="#tick" x="217" y="561"/><text class="feature" x="241" y="566">Check 4</text>
  </g>

  <!-- Security and Compliance -->
  <g class="quadrant quadrant--security">
    <text class="panel-title panel-title--large" x="875" y="307" textLength="525" lengthAdjust="spacingAndGlyphs">Security and Compliance</text>
    <line class="rule rule--security" x1="878" y1="330" x2="1402" y2="330"/>
    <text class="panel-text">
      <tspan x="875" y="374">Benefit from tailored cloud solutions, secure data</tspan>
      <tspan x="875" y="399">storage, and expert disaster recovery planning for</tspan>
      <tspan x="875" y="424">reliable and scalable IT operations.</tspan>
    </text>
    <use href="#tick" x="894" y="480"/><text class="feature" x="932" y="485">Custom Cloud Solutions</text>
    <use href="#tick" x="894" y="505"/><text class="feature" x="932" y="510">Secure Data Storage</text>
    <use href="#tick" x="894" y="531"/><text class="feature" x="932" y="536">Expert Disaster Recovery</text>
    <use href="#tick" x="894" y="556"/><text class="feature" x="932" y="561">Check 4</text>
  </g>

  <!-- Enterprise Resource Planning -->
  <g class="quadrant quadrant--erp">
    <text class="panel-title panel-title--small" x="218" y="1135" textLength="501" lengthAdjust="spacingAndGlyphs">Enterprise Resource Planning</text>
    <line class="rule rule--erp" x1="222" y1="1156" x2="711" y2="1156"/>
    <text class="panel-text" text-anchor="end">
      <tspan x="714" y="1202">Simplify management across finance, sales, and</tspan>
      <tspan x="714" y="1227">operations, enabling better decision-making</tspan>
      <tspan x="714" y="1253">and improved productivity.</tspan>
    </text>
    <use href="#tick" x="238" y="1321"/><text class="feature" x="267" y="1326">Integrated Business Processes</text>
    <use href="#tick" x="238" y="1347"/><text class="feature" x="267" y="1352">Enhanced Decision-Making</text>
    <use href="#tick" x="238" y="1372"/><text class="feature" x="267" y="1377">Productivity Improvement</text>
    <use href="#tick" x="238" y="1398"/><text class="feature" x="267" y="1403">Check 4</text>
  </g>

  <!-- Digital Transformation -->
  <g class="quadrant quadrant--digital">
    <text class="panel-title panel-title--small" x="894" y="1142" textLength="416" lengthAdjust="spacingAndGlyphs">Digital Transformation</text>
    <line class="rule rule--digital" x1="898" y1="1164" x2="1388" y2="1164"/>
    <text class="panel-text">
      <tspan x="895" y="1212">Turn scanned documents into easily searchable</tspan>
      <tspan x="895" y="1237">digital archives, boosting efficiency and</tspan>
      <tspan x="895" y="1263">accessibility.</tspan>
    </text>
    <use href="#tick" x="905" y="1330"/><text class="feature" x="944" y="1335">Instant searchable Archives with OCR</text>
    <use href="#tick" x="905" y="1355"/><text class="feature" x="944" y="1360">Automated Document Classification</text>
    <use href="#tick" x="905" y="1381"/><text class="feature" x="944" y="1386">TeamPortal and Cloud Blob Ready</text>
    <use href="#tick" x="905" y="1406"/><text class="feature" x="944" y="1411">Check 4</text>
  </g>

  <!-- Central hub -->
  <g class="hub">
    <circle class="hub-ring" cx="805" cy="835" r="229"/>
    <text class="hub-title" text-anchor="middle" x="809" y="812" textLength="262" lengthAdjust="spacingAndGlyphs">Super</text>
    <text class="hub-title" text-anchor="middle" x="807" y="894" textLength="355" lengthAdjust="spacingAndGlyphs">Product</text>
  </g>

  <!-- Hub icons -->
  <g class="hub-icon hub-icon--docs">
    <circle class="icon-halo" cx="641" cy="669" r="84"/>
    <circle class="icon-disc--docs" cx="641" cy="669" r="57"/>
    <path class="glyph" d="M620 638 H650 L662 650 V698 H620 Z M650 638 V650 H662"/>
    <path class="glyph" d="M628 657 H654 M628 665 H654 M628 673 H654 M628 681 H654 M628 689 H654"/>
  </g>
  <g class="hub-icon hub-icon--security">
    <circle class="icon-halo" cx="971" cy="669" r="84"/>
    <circle class="icon-disc--security" cx="971" cy="669" r="57"/>
    <path class="glyph" d="M971 633 L998 643 V668 C998 688 986 699 971 705 C956 699 944 688 944 668 V643 Z" stroke-width="4.5"/>
    <path class="glyph" d="M959 669 L968 678 L984 660" stroke-width="5.5"/>
  </g>
  <g class="hub-icon hub-icon--erp">
    <circle class="icon-halo" cx="641" cy="999" r="84"/>
    <circle class="icon-disc--erp" cx="641" cy="999" r="57"/>
    <path class="glyph" d="M627 979 V1022 H662 V979 Z"/>
    <path class="glyph" d="M620 972 H652 V977 M620 972 V1015 H625"/>
    <path class="glyph" d="M633 989 H656 M633 996 H656 M633 1003 H656 M633 1010 H656"/>
  </g>
  <g class="hub-icon hub-icon--digital">
    <circle class="icon-halo" cx="971" cy="999" r="84"/>
    <circle class="icon-disc--digital" cx="971" cy="999" r="57"/>
    <path class="glyph" d="M939 989 A46 46 0 0 1 1003 989" stroke-width="7"/>
    <path class="glyph" d="M949 999 A31 31 0 0 1 993 999" stroke-width="7"/>
    <path class="glyph" d="M959 1009 A17 17 0 0 1 983 1009" stroke-width="7"/>
    <circle class="glyph-solid" cx="971" cy="1020" r="8"/>
  </g>
</svg>
</body>
</html>
```